Walk Beside The River

Business Card design

Target Market(s)

People who require support in the commnity

Industry/Entity Type

Mental Health Support

Contact Information for Business Card

Mental Health Support Rosalind Tavener walkbesidetheriver@mailcove.com.au 0481 637 092 PO Box 926 Larkhaven QLD 4619

Colors
6B429C
8869AF
B7A5CE
E3DAEB
F3F0F8

Requirements
Must have
• Logo & details listed above
Should not have
• No red or orange

```html
<!DOCTYPE html>
<html lang="en">
<head>
<meta charset="utf-8">
<title>Walk Beside The River – Business Card</title>
<link href="https://fonts.googleapis.com/css2?family=Montserrat:wght@800&family=Open+Sans:wght@400;600&display=swap" rel="stylesheet">
<style>
  :root {
    --stage: #2b2a2f;
    --card-dark: #1f1e23;
    --purple: #6b429c;
    --purple-mid: #8869af;
    --yellow: #f2e829;
    --gold: #e9c640;
    --white: #ffffff;
  }
  html, body {
    margin: 0;
    width: 1200px;
    height: 780px;
    overflow: hidden;
    background: var(--stage);
  }
  .canvas {
    position: relative;
    width: 1200px;
    height: 780px;
  }
  .card {
    position: absolute;
    top: 235px;
    width: 540px;
    height: 310px;
    border-radius: 20px;
    overflow: hidden;
    box-sizing: border-box;
  }
  .card-back {
    left: 40px;
    background: linear-gradient(135deg, #f6ef5a 0%, var(--yellow) 45%, var(--gold) 100%);
  }
  .card-front {
    left: 620px;
    background: var(--card-dark);
    border: 2px solid var(--yellow);
  }
  .front-shapes {
    position: absolute;
    inset: 0;
    width: 100%;
    height: 100%;
  }
  .holder {
    position: absolute;
    top: 22px;
    right: 76px;
    text-align: right;
  }
  .holder-name {
    margin: 0;
    font-family: "Montserrat", sans-serif;
    font-weight: 800;
    font-size: 28px;
    line-height: 1;
    color: var(--yellow);
    letter-spacing: 0.5px;
  }
  .holder-name .surname { color: var(--purple-mid); }
  .holder-role {
    margin: 6px 0 0;
    font-family: "Open Sans", sans-serif;
    font-size: 14px;
    color: var(--white);
  }
  .brand {
    position: absolute;
    left: 26px;
    top: 58px;
    display: flex;
    align-items: center;
    gap: 10px;
  }
  .brand-dot {
    width: 60px;
    height: 60px;
    border-radius: 50%;
    background: var(--purple);
  }
  .brand-name {
    font-family: "Open Sans", sans-serif;
    font-weight: 600;
    font-size: 15px;
    color: var(--white);
  }
  .details {
    position: absolute;
    left: 30px;
    top: 136px;
    font-family: "Open Sans", sans-serif;
    color: var(--white);
  }
  .service, .person {
    margin: 0;
    font-size: 15px;
    line-height: 21px;
  }
  .contact-list {
    list-style: none;
    margin: 8px 0 0;
    padding: 0;
  }
  .contact-list li {
    display: flex;
    align-items: center;
    gap: 8px;
    font-size: 14px;
    line-height: 22px;
  }
  .contact-icon {
    width: 13px;
    height: 13px;
    flex: none;
  }
</style>
</head>
<body>
<main class="canvas">
  <section class="card card-back" role="img" aria-label="Card back: repeating gold star pattern on bright yellow"></section>

  <section class="card card-front">
    <svg class="front-shapes" viewBox="0 0 536 306" preserveAspectRatio="none" aria-hidden="true">
      <rect class="name-tab" x="464" y="0" width="30" height="40" fill="var(--purple)"/>
      <path class="purple-sweep" d="M536 92 C468 110 430 160 412 220 C396 270 320 300 230 306 L536 306 Z" fill="var(--purple)"/>
      <path class="yellow-swoosh" d="M150 290 C250 286 360 262 440 196 C400 250 310 292 170 302 Z" fill="var(--yellow)"/>
    </svg>

    <div class="holder">
      <h1 class="holder-name">Danica <span class="surname">Holloway</span></h1>
      <p class="holder-role">CEO/Director</p>
    </div>

    <div class="brand">
      <span class="brand-dot"></span>
      <span class="brand-name">Walk Beside The River</span>
    </div>

    <div class="details">
      <p class="service">Mental Health Support</p>
      <p class="person">Rosalind Tavener</p>
      <ul class="contact-list">
        <li>
          <svg class="contact-icon" viewBox="0 0 12 12" aria-hidden="true"><path d="M2.5 1 L4.5 1 L5 3.5 L3.8 4.4 C4.5 6 6 7.5 7.6 8.2 L8.5 7 L11 7.5 L11 9.5 C11 10.3 10.3 11 9.5 11 C5 11 1 7 1 2.5 C1 1.7 1.7 1 2.5 1 Z" fill="var(--yellow)"/></svg>
          0481 637 092
        </li>
        <li>
          <svg class="contact-icon" viewBox="0 0 12 12" aria-hidden="true"><rect x="0.8" y="2.5" width="10.4" height="7.5" rx="1" fill="none" stroke="var(--yellow)" stroke-width="1.2"/><path d="M1 3 L6 6.8 L11 3" fill="none" stroke="var(--yellow)" stroke-width="1.2"/></svg>
          walkbesidetheriver@mailcove.com.au
        </li>
        <li>
          <svg class="contact-icon" viewBox="0 0 12 12" aria-hidden="true"><path d="M6 11.5 C6 11.5 2 7.2 2 4.6 A4 4 0 0 1 10 4.6 C10 7.2 6 11.5 6 11.5 Z" fill="var(--yellow)"/><circle cx="6" cy="4.6" r="1.5" fill="var(--card-dark)"/></svg>
          PO Box 926 Larkhaven QLD 4619
        </li>
      </ul>
    </div>
  </section>
</main>
</body>
</html>
```